Poster announcing University Web Analytics talk

We need a poster to announce an upcoming talk on Web Analytics at the local University. The event is addressed to final year students (mostly in Informatic Engineering, although other majors are wellcomed as well) who may be interested in specializing in this rising field.

The poster should present a brief list of the points we'll be addressing, as well as the place and time of the meeting. Also, it must feature our company logo (check the uploads section to find it) and our website url: http://www.brasslanternworks.net.

Texts for the poster:

Headline: "Get specialized in Web & Mobile Analytics"

Topics that will be covered:
- Introduction to Analytics, market, work opportunities
- Know the basics of an Analytics project: planning, phases, implementation
- Job bank: bring your CV!

Event information: "Thursday 20th June at the Facultad de Cartografía, Universidad de Valdemora". [A space to fill with the time must be provided here]

However, we'll be translating all the text to Spanish later, so we'll need a file where we can modify the text layers.
Updates

Thanks to all of you, we're receiving so many excellent works!

We had missed to include some important information on the brief - we didn't say anything about the colors, and we have been getting some designs based in dark colors. Now, it doesn't matter what colors you use, but we'd like better a brighter design (no matter if the color combination is more playful or either rather serious). This is going to be a free talk addressed to last year students, so we want to transmit a feeling of an interesting, easy and entertaining afternoon.

I hope these comments are helpful, please reach me with any question or comment. 

Thanks a lot again!
Nuria 
BL team

Target Market(s)

Final year students and graduates.

Industry/Entity Type

Bank

Requirements
Must have
• Design must be submitted in vector format, preferably .psd. We must be able to modify the text layers. Our logo (check the files section) and website url (http://www.brasslanternworks.net) must be included
Nice to have
• Illustrations making reference to Analytics (charts, statistics, code) and/or the internet will be a plus!

```html
<!DOCTYPE html>
<html lang="en">
<head>
<meta charset="utf-8">
<title>Get specialized in Web &amp; Mobile Analytics</title>
<link href="https://fonts.googleapis.com/css2?family=Roboto+Condensed:wght@400;700&display=swap" rel="stylesheet">
<style>
  :root{
    --paper-top:#f4f4f4;
    --paper-bottom:#dedede;
    --ink:#6b6b6b;
    --ink-dark:#555;
    --white:#fff;
    --band-blue:#1f6fc0;
    --band-navy:#1c3f9c;
    --band-green-dark:#1d8a3a;
    --band-green:#47b632;
    --band-grey:#4d4d4d;
    --brand-green:#6aa82e;
    --art-1:#f2a23a;
    --art-2:#3a8fd6;
    --art-3:#5cb845;
    --art-4:#d94a3c;
  }
  *{margin:0;padding:0;box-sizing:border-box}
  html,body{width:849px;height:1200px;overflow:hidden}
  body{font-family:"Roboto Condensed",Arial,sans-serif}
  .poster{
    position:relative;width:849px;height:1200px;overflow:hidden;
    background:linear-gradient(180deg,var(--paper-top),var(--paper-bottom));
  }
  .analytics-art{
    position:absolute;left:0;top:0;width:300px;height:1200px;
    background:
      radial-gradient(circle at 90px 260px,rgba(217,74,60,.55),transparent 120px),
      radial-gradient(circle at 170px 620px,rgba(242,162,58,.55),transparent 150px),
      radial-gradient(circle at 60px 900px,rgba(58,143,214,.5),transparent 160px),
      radial-gradient(circle at 200px 1050px,rgba(92,184,69,.45),transparent 140px),
      linear-gradient(90deg,rgba(200,205,215,.9),rgba(240,240,240,0));
    -webkit-mask-image:linear-gradient(90deg,#000 70%,transparent);
    mask-image:linear-gradient(90deg,#000 70%,transparent);
  }
  .headline{
    position:absolute;left:313px;top:172px;width:500px;
    font-weight:700;font-size:48px;line-height:1.08;color:var(--ink);
    letter-spacing:-.3px;
  }
  .topic-band{
    position:absolute;left:170px;display:flex;align-items:center;
    padding-left:143px;color:var(--white);font-weight:700;
    clip-path:polygon(0 0,calc(100% - 36px) 0,100% 50%,calc(100% - 36px) 100%,0 100%);
  }
  .topic-band span{font-size:19px;line-height:1.25}
  .topic-band--intro{top:300px;height:82px;width:535px;
    background:linear-gradient(90deg,rgba(31,111,192,0),var(--band-blue) 30%)}
  .topic-band--basics{top:392px;height:78px;width:440px;
    background:linear-gradient(90deg,rgba(28,63,156,0),var(--band-navy) 30%)}
  .topic-band--planning{top:482px;height:64px;width:465px;
    background:linear-gradient(90deg,rgba(29,138,58,0),var(--band-green-dark) 30%)}
  .topic-band--jobs{top:555px;height:80px;width:525px;
    background:linear-gradient(90deg,rgba(71,182,50,0),var(--band-green) 30%)}
  .topic-band--cv{top:648px;height:82px;width:390px;
    background:linear-gradient(90deg,rgba(77,77,77,0),var(--band-grey) 30%)}
  .topic-band--cv span{font-size:32px}
  .event-info{
    position:absolute;left:307px;top:760px;width:480px;
    font-weight:700;font-size:25px;line-height:1.22;color:var(--ink);
  }
  .brand{
    position:absolute;left:307px;top:895px;display:flex;align-items:center;gap:14px;
  }
  .brand-mark{width:52px;height:52px;background:var(--brand-green)}
  .brand-name{font-weight:700;font-size:34px;color:var(--brand-green);line-height:1}
  .website{
    position:absolute;left:307px;top:1000px;
    font-weight:700;font-size:23px;color:var(--ink-dark);
  }
</style>
</head>
<body>
<main class="poster">
  <div class="analytics-art" role="img" aria-label="Collage of analytics charts, arrows, pie charts and web browser icons"></div>

  <h1 class="headline">Get specialized in<br>Web &amp; Mobile Analytics</h1>

  <div class="topic-band topic-band--intro"><span>Introduction to Analytics, market,<br>work opportunities</span></div>
  <div class="topic-band topic-band--basics"><span>Know the basics of an Analytics<br>project</span></div>
  <div class="topic-band topic-band--planning"><span>Planning, phases, implementation</span></div>
  <div class="topic-band topic-band--jobs"><span>Job bank</span></div>
  <div class="topic-band topic-band--cv"><span>bring your CV!</span></div>

  <p class="event-info">Thursday 20th June at the Facultad de Cartografía,<br>Universidad de Valdemora<br>Time here</p>

  <div class="brand">
    <div class="brand-mark"></div>
    <div class="brand-name">brass lantern works</div>
  </div>

  <p class="website">www.brasslanternworks.net</p>
</main>
</body>
</html>
```